Transform Your Giving

I need a tri-fold brochure that will fit in a standard number 10 business envelope. Meadowlark and Allied Services is a charitable nonprofit. The goal of this brochure is to stimulate people into thinking about other ways to make a donation. The design should communicate the essential information on donation options, create a sense of professional integrity, be graphically sharp, easy to read and laid out in a way that doesn't make the material appear crowded.

```html
<!DOCTYPE html>
<html lang="en">
<head>
<meta charset="utf-8">
<title>Transform Your Giving – Tri-fold Brochure</title>
<link rel="stylesheet" href="https://fonts.googleapis.com/css2?family=Fira+Sans:ital,wght@0,400;0,500;0,600;0,700;1,600;1,700&family=Roboto:wght@400;500&family=Montserrat:wght@300;400&display=swap">
<style>
:root{
  --navy:#2c2a7f;
  --navy-deep:#24226b;
  --green:#4cb848;
  --ink:#1f1f2e;
  --paper:#ffffff;
  --backdrop:#7b7b7b;
  --muted:#a9abb3;
}
*{margin:0;padding:0;box-sizing:border-box}
html,body{width:1096px;height:1200px;overflow:hidden;background:var(--backdrop)}
body{position:relative;font-family:"Roboto",sans-serif;color:var(--ink)}
.sheet{position:absolute;left:205px;width:687px;height:516px;display:flex;background:var(--paper)}
.sheet--outside{top:63px}
.sheet--inside{top:621px}
.panel{position:relative;width:229px;height:516px;overflow:hidden;flex:none}
.panel--navy{background:linear-gradient(180deg,#2a2680 0%,#28257a 40%,#2c2a80 100%);color:#fff}
.sheet--inside .panel:nth-child(1){background:linear-gradient(90deg,#fff 85%,#eeeef0 100%)}
.sheet--inside .panel:nth-child(2){background:linear-gradient(90deg,#f1f1f3 0%,#fff 12%,#fff 88%,#f1f1f3 100%)}
.sheet--inside .panel:nth-child(3){background:linear-gradient(90deg,#ececee 0%,#fff 14%)}
.abs{position:absolute}
.photo{position:absolute;left:0;width:229px}
.curve{position:absolute;left:0;width:229px;display:block}

/* type */
.h-caps{font-family:"Fira Sans",sans-serif;font-weight:700;color:var(--navy);text-transform:uppercase}
.lead{font-family:"Roboto",sans-serif;font-size:10.1px;line-height:12.9px;color:var(--ink)}
.body{font-size:8.4px;line-height:10.9px;color:#2a2a35}
.body p+p{margin-top:9px}
.howto{font-family:"Fira Sans",sans-serif;font-weight:700;font-size:10.4px;color:var(--navy)}
.sec-title{font-family:"Fira Sans",sans-serif;font-weight:600;font-size:9.4px;line-height:11.6px;color:var(--navy)}
.sec-tag{font-family:"Fira Sans",sans-serif;font-weight:600;font-style:italic;font-size:8.8px;line-height:11.2px;color:var(--green)}

/* icons */
.badge{position:absolute;border-radius:50%;background:var(--navy);display:flex;align-items:center;justify-content:center}
.badge svg{display:block}
.badge--sm{width:42px;height:42px;border:1.5px solid #fff;box-shadow:0 0 0 1.2px var(--navy)}
.badge--ring{width:50px;height:50px;border:4px solid #fff;box-shadow:0 0 0 2.2px var(--green)}
.option-label{position:absolute;font-family:"Fira Sans",sans-serif;font-weight:600;font-size:10.3px;line-height:12.6px;color:var(--ink)}
.option-label--caps{font-weight:600;text-transform:uppercase;text-align:center;font-size:10.4px;line-height:13px}
.dots{position:absolute;border-top:1.3px dotted var(--navy)}
.dots--v{border-top:none;border-left:1.3px dotted var(--navy)}

/* wordmark */
.wordmark{position:absolute;left:0;width:229px;text-align:center;font-family:"Fira Sans",sans-serif;font-weight:700}

/* contact */
.contact{position:absolute;left:0;width:229px;text-align:center;font-family:"Montserrat",sans-serif;font-weight:400;font-size:8.4px;line-height:10.8px;color:#fff}
.contact-dot{width:8px;height:8px;border-radius:50%;background:var(--green);margin:0 auto 3px;display:flex;align-items:center;justify-content:center}
.contact-dot svg{display:block}
.bullets{list-style:none}
.bullets li{position:relative;padding-left:10px}
.bullets li+li{margin-top:5px}
.bullets li::before{content:"";position:absolute;left:0;top:2px;width:6px;height:6px;border-radius:50%;background:var(--navy)}
.bullets li::after{content:"";position:absolute;left:1.6px;top:3.6px;width:2.4px;height:1.3px;border-left:1px solid #fff;border-bottom:1px solid #fff;transform:rotate(-45deg)}
</style>
</head>
<body>

<svg width="0" height="0" style="position:absolute" aria-hidden="true">
  <defs>
    <symbol id="i-coin" viewBox="0 0 24 24"><g fill="none" stroke="#fff" stroke-width="1.4" stroke-linejoin="round"><path d="M8 5h6a3.2 3.2 0 0 1 0 6.5H8zM8 11.5h7a3.3 3.3 0 0 1 0 6.5H8zM8 5v13M10 3v2M13 3v2M10 18v2M13 18v2M6 5h2M6 18h2"/></g></symbol>
    <symbol id="i-bank" viewBox="0 0 24 24"><g fill="none" stroke="#fff" stroke-width="1.3" stroke-linejoin="round"><path d="M3 8.5 12 4l9 4.5zM4 8.5h16M5.5 10.5v7M9 10.5v7M12 10.5v7M15 10.5v7M18.5 10.5v7M3.5 18h17M2.5 20h19"/></g></symbol>
    <symbol id="i-gift" viewBox="0 0 24 24"><g fill="none" stroke="#fff" stroke-width="1.3" stroke-linejoin="round"><path d="M3.5 8h17v3.5h-17zM5 11.5h14V20H5zM12 8v12M12 8c-2-3-5-4-5-1.8S10 8 12 8zM12 8c2-3 5-4 5-1.8S14 8 12 8z"/></g></symbol>
    <symbol id="i-chart" viewBox="0 0 24 24"><g fill="none" stroke="#fff" stroke-width="1.3" stroke-linejoin="round"><path d="M4 20h16M5 14h3v6H5zM10.5 11h3v9h-3zM16 8h3v12h-3zM4 12 10 7l3 2 6-5M16 4h3v3"/></g></symbol>
    <symbol id="i-annuity" viewBox="0 0 24 24"><g fill="none" stroke="#fff" stroke-width="1.2" stroke-linejoin="round"><path d="M3.5 6h17v14h-17zM3.5 10h17M7 4v3.5M17 4v3.5M6 13h2v2H6zM11 13h2v2h-2zM16 13h2v2h-2zM6 17h2M11 17h2M16 17h2"/><circle cx="12" cy="6.5" r="3.4" fill="#2c2a7f"/><path d="M13.2 5.3c-.4-.5-2.4-.6-2.4.4s2.4.6 2.4 1.6-2 1-2.5.4M12 4.2v.8M12 8v.8"/></g></symbol>
  </defs>
</svg>

<!-- ========== OUTSIDE SHEET ========== -->
<section class="sheet sheet--outside" aria-label="Brochure outside">

  <!-- Inside flap: impact -->
  <div class="panel panel--impact">
    <div class="photo" style="top:0;height:225px;background:linear-gradient(135deg,#efe9e2 0%,#d9cfc6 45%,#b8a79a 75%,#d6cfc8 100%)" role="img" aria-label="Photo of a young woman helping an elderly man on a laptop"></div>
    <svg class="curve" style="top:200px" height="30" viewBox="0 0 229 30" preserveAspectRatio="none" aria-hidden="true">
      <path d="M0 30 Q114.5 -6 229 30 Z" fill="#fff"/>
      <path d="M0 30 Q114.5 -6 229 30" fill="none" stroke="#4cb848" stroke-width="3"/>
    </svg>
    <h2 class="abs h-caps" style="left:18px;top:219px;font-size:12.3px;letter-spacing:.1px">The Impact of Your Gift</h2>
    <p class="abs lead" style="left:18px;top:234px;width:196px">Your generosity drives our mission. With every Smart gift you’re supporting Meadowlark and Allied Services. Join our community of Smart Givers today and make an enduring impact. With Smart Giving your generosity reaches further.&nbsp; Begin your Smart Giving journey with us today.</p>

    <span class="dots dots--v" style="left:38px;top:395px;height:9px"></span>
    <span class="dots dots--v" style="left:38px;top:445px;height:9px"></span>
    <span class="dots dots--v" style="left:130px;top:395px;height:9px"></span>
    <div class="badge badge--sm" style="left:17px;top:353px"><svg width="24" height="24"><use href="#i-coin"/></svg></div>
    <div class="badge badge--sm" style="left:17px;top:403px"><svg width="24" height="24"><use href="#i-bank"/></svg></div>
    <div class="badge badge--sm" style="left:17px;top:453px"><svg width="22" height="22"><use href="#i-gift"/></svg></div>
    <div class="badge badge--sm" style="left:109px;top:353px"><svg width="24" height="24"><use href="#i-chart"/></svg></div>
    <div class="badge badge--sm" style="left:109px;top:403px"><svg width="24" height="24"><use href="#i-annuity"/></svg></div>
    <span class="option-label" style="left:64px;top:368px">Crypto</span>
    <span class="option-label" style="left:64px;top:418px">DAF’s</span>
    <span class="option-label" style="left:64px;top:468px">QCDs</span>
    <span class="option-label" style="left:157px;top:362px">Stocks &amp;<br>Securities</span>
    <span class="option-label" style="left:157px;top:412px">Charitable<br>Annuity</span>
    <div class="wordmark" style="left:110px;width:112px;top:458px;font-size:9px;line-height:11px;font-weight:600;color:var(--muted)">Meadowlark and Allied Services</div>
  </div>

  <!-- Back panel: contact -->
  <div class="panel panel--navy">
    <div class="photo" style="top:90px;height:120px;background:radial-gradient(ellipse at 45% 55%,rgba(70,80,170,.55) 0%,rgba(42,38,128,0) 70%)" role="img" aria-label="Faint photo of hands reaching toward each other"></div>
    <p class="abs" style="left:14px;top:18px;width:201px;text-align:center;font-family:'Fira Sans',sans-serif;font-size:9.1px;line-height:11.5px">To learn more about Smart Giving Options and how they can benefit you and Meadowlark and Allied Services, please reach out to our team.&nbsp; We’re here to help you navigate these giving methods and answer any question you may have.</p>
    <p class="abs" style="left:14px;top:97px;width:201px;text-align:center;font-family:'Montserrat',sans-serif;font-weight:300;font-size:8.6px;line-height:11.5px">Being kind to others is a way of<br>being good to yourself.<br>Helen Marsh</p>
    <p class="abs" style="left:10px;top:201px;width:209px;text-align:center;font-family:'Fira Sans',sans-serif;font-size:9.1px;line-height:11.2px">If you do not have a will, go to<br><span style="color:var(--green);text-decoration:underline">www.Willnest.com.</span><br>In 20 minutes you can have a legal will – for free.</p>
    <div class="wordmark" style="top:262px;font-size:14px;line-height:17px;color:#fff">Meadowlark and<br>Allied Services</div>
    <h3 class="abs" style="left:0;width:229px;top:328px;text-align:center;font-family:'Fira Sans',sans-serif;font-weight:700;font-size:10.5px;text-decoration:underline;text-transform:uppercase">Contact Us</h3>
    <p class="abs" style="left:0;width:229px;top:348px;text-align:center;font-family:'Fira Sans',sans-serif;font-weight:600;font-size:8.8px;line-height:11.4px;color:var(--green)">Have more question? Please contact us at<br>Meadowlark and Allied Services</p>
    <div class="contact" style="top:374px">
      <div class="contact-dot"><svg width="5" height="5" viewBox="0 0 10 10"><path d="M5 1a3 3 0 0 1 3 3c0 2-3 5-3 5S2 6 2 4a3 3 0 0 1 3-3z" fill="#fff"/></svg></div>
      1420 Prairie View Rd.<br>Suite 6 Fargo, ND&nbsp; 58102
    </div>
    <div class="contact" style="top:409px">
      <div class="contact-dot"><svg width="5" height="5" viewBox="0 0 10 10"><path d="M2 1h2l1 2.5-1.2 1a5 5 0 0 0 2.7 2.7l1-1.2L10 7v2c-4.5.5-9-4-8-8z" fill="#fff"/></svg></div>
      701-555-0142 (ext. 100)
    </div>
    <div class="contact" style="top:434px">
      <div class="contact-dot"><svg width="5" height="5" viewBox="0 0 10 10"><path d="M1 2.5h8v5H1zM1 2.5 5 5.5l4-3" fill="none" stroke="#fff" stroke-width="1.2"/></svg></div>
      jmorrow@meadowlarkas.org
    </div>
    <div class="contact" style="top:459px">
      <div class="contact-dot"><svg width="5" height="5" viewBox="0 0 10 10"><circle cx="5" cy="5" r="4" fill="none" stroke="#fff" stroke-width="1"/><path d="M1 5h8M5 1c-2 2.5-2 5.5 0 8M5 1c2 2.5 2 5.5 0 8" fill="none" stroke="#fff" stroke-width=".8"/></svg></div>
      www.meadowlarkas.org
    </div>
    <div class="abs" style="left:0;width:229px;top:490px;display:flex;justify-content:center;align-items:center;gap:3px;font-family:'Fira Sans',sans-serif;font-weight:700;font-size:9px">
      <span style="text-decoration:underline;margin-right:2px">FOLLOW US:</span>
      <span style="width:9px;height:9px;border-radius:50%;background:var(--green)"></span>
      <span style="width:9px;height:9px;border-radius:50%;background:var(--green)"></span>
    </div>
  </div>

  <!-- Front cover -->
  <div class="panel panel--cover">
    <h1 class="abs" style="left:0;width:229px;top:14px;text-align:center;font-family:'Fira Sans',sans-serif;font-weight:700;font-size:17px;line-height:20px;color:var(--navy)">Transform Your Giving<br><span style="color:var(--green)">Be Strategic, Be Smart</span></h1>
    <p class="abs" style="left:0;width:229px;top:57px;text-align:center;font-family:'Fira Sans',sans-serif;font-weight:600;font-size:8.6px;line-height:11.4px;color:var(--navy)">Discover the impact of Smart Giving with<br>Meadowlark and Allied Services</p>
    <div class="photo" style="top:90px;height:210px;background:linear-gradient(135deg,#6f9a45 0%,#9cbf6a 35%,#d8c9b4 60%,#b89a55 100%)" role="img" aria-label="Photo of a smiling senior couple embracing outdoors"></div>
    <svg class="curve" style="top:88px" height="28" viewBox="0 0 229 28" preserveAspectRatio="none" aria-hidden="true">
      <path d="M0 0H229V28Q114.5 -6 0 28Z" fill="#fff"/>
      <path d="M0 28Q114.5 -6 229 28" fill="none" stroke="#4cb848" stroke-width="3"/>
    </svg>
    <svg class="curve" style="top:272px" height="34" viewBox="0 0 229 34" preserveAspectRatio="none" aria-hidden="true">
      <path d="M0 34 Q114.5 -8 229 34 Z" fill="#fff"/>
      <path d="M0 34 Q114.5 -8 229 34" fill="none" stroke="#4cb848" stroke-width="3"/>
    </svg>
    <span class="dots" style="left:66px;top:310px;width:28px"></span>
    <span class="dots" style="left:136px;top:310px;width:26px"></span>
    <span class="dots" style="left:99px;top:370px;width:32px"></span>
    <div class="badge badge--sm" style="left:24px;top:289px"><svg width="24" height="24"><use href="#i-coin"/></svg></div>
    <div class="badge badge--sm" style="left:94px;top:289px"><svg width="24" height="24"><use href="#i-bank"/></svg></div>
    <div class="badge badge--sm" style="left:161px;top:289px"><svg width="22" height="22"><use href="#i-gift"/></svg></div>
    <div class="badge badge--sm" style="left:57px;top:349px"><svg width="24" height="24"><use href="#i-chart"/></svg></div>
    <div class="badge badge--sm" style="left:131px;top:349px"><svg width="24" height="24"><use href="#i-annuity"/></svg></div>
    <span class="option-label option-label--caps" style="left:15px;width:60px;top:335px">Crypto</span>
    <span class="option-label option-label--caps" style="left:85px;width:60px;top:335px">DAF’s</span>
    <span class="option-label option-label--caps" style="left:152px;width:60px;top:335px">QCDs</span>
    <span class="option-label option-label--caps" style="left:38px;width:80px;top:394px">Stocks &amp;<br>Securities</span>
    <span class="option-label option-label--caps" style="left:112px;width:80px;top:394px">Charitable<br>Annuity</span>
    <div class="wordmark" style="top:446px;font-size:16px;line-height:19px;color:var(--navy)">Meadowlark and<br>Allied Services</div>
  </div>
</section>

<!-- ========== INSIDE SHEET ========== -->
<section class="sheet sheet--inside" aria-label="Brochure inside">

  <!-- Stocks + DAF -->
  <div class="panel">
    <p class="abs" style="left:18px;top:16px;width:192px;font-size:9px;line-height:11.5px">We would like to introduce you to five Strategic and Smart ways to give that could potentially be more beneficial to you compared to traditional cash donations. We encourage you to keep this information as a guide for your future contributions.</p>

    <div class="badge badge--ring" style="left:17px;top:91px"><svg width="28" height="28"><use href="#i-chart"/></svg></div>
    <h3 class="abs sec-title" style="left:74px;top:92px;width:150px">Gifts of Stocks or Appreciated Assets Strategic &amp; Smart</h3>
    <p class="abs sec-tag" style="left:74px;top:120px;width:150px">Consider your long-term publicly traded stock as a way to give to your favorite charity.</p>
    <p class="abs body" style="left:18px;top:160px;width:196px">You can make a significantly bigger impact when you donate long-term appreciated securities, including stock, mutual funds, &amp; bonds, directly to your favorite charity.</p>
    <h4 class="abs howto" style="left:18px;top:208px">How Does It Work?</h4>
    <p class="abs body" style="left:18px;top:222px;width:196px">When you donate stock to a charity, you will generally take a tax deduction for the full market value. Because you are donating stock, your contribution &amp; tax deduction may be significantly higher than contributing the after-tax proceeds. The same benefits apply when you donate mutual funds or bonds.</p>

    <div class="badge badge--ring" style="left:17px;top:314px"><svg width="28" height="28"><use href="#i-bank"/></svg></div>
    <h3 class="abs sec-title" style="left:74px;top:314px;width:150px">Donor-Advised Fund (DAF)<br>Strategic &amp; Smart</h3>
    <p class="abs sec-tag" style="left:74px;top:342px;width:150px">Consider a DAF – a simple, flexible, and tax-advantageous way to give to your favorite charities.</p>
    <p class="abs body" style="left:18px;top:382px;width:196px;font-size:8.8px;line-height:11.2px">A Donor-Advised Fund (DAF), is like a charitable investment account for the sole purpose of supporting your favorite charities.</p>
    <h4 class="abs howto" style="left:18px;top:421px">How Does It Work?</h4>
    <p class="abs body" style="left:18px;top:435px;width:196px">You establish a DAF &amp; contribute cash, stocks, or non-publicly traded assets, cryptocurrency, &amp; private company stock to be eligible for an immediate tax deduction. Those funds are contributed for tax-free growth. You can recommend grants be made from your DAF to any IRS qualified public charity.</p>
  </div>

  <!-- QCD + Annuity -->
  <div class="panel">
    <div class="badge badge--ring" style="left:17px;top:18px"><svg width="26" height="26"><use href="#i-gift"/></svg></div>
    <h3 class="abs sec-title" style="left:75px;top:19px;width:150px;font-size:8.8px;line-height:11.2px">Qualified Charitable Distributions (QCDs) Strategic &amp; Smart</h3>
    <p class="abs sec-tag" style="left:75px;top:43px;width:150px;font-size:8.4px;line-height:10.9px">Consider a QCD – when planning your IRA withdrawal strategy... &amp; donate to your favorite charity.</p>
    <p class="abs body" style="left:17px;top:81px;width:198px">IRA owners at age 70 ½ or over can transfer dollars from their IRA to charity tax-free each year. These transfers known as Qualified Charitable Distributions (QCDs) offer eligible older Americans a great way to easily give to charity.</p>
    <h4 class="abs howto" style="left:17px;top:141px">How Does It Work?</h4>
    <p class="abs body" style="left:17px;top:156px;width:198px">Are you 72 and required to take a minimum distribution (RMD) from your IRA but do not need the funds? Consider a Qualified Charitable Distribution. Normally, distributions from a traditional IRA are taxable when received. With a QCD, these distributions become tax-free when paid directly from the IRA to your favorite eligible charity. An IRA owner wishing to make a QCD should contact their IRA trustee, allowing time to complete the transaction before the end of the year to receive the tax benefit.</p>

    <div class="badge badge--ring" style="left:17px;top:294px"><svg width="28" height="28"><use href="#i-annuity"/></svg></div>
    <h3 class="abs sec-title" style="left:78px;top:294px;width:140px;font-size:8.8px;line-height:11.2px">Charitable Gift Annuity<br>Strategic &amp; Smart</h3>
    <p class="abs sec-tag" style="left:78px;top:317px;width:140px;font-size:8.4px;line-height:10.9px">Consider establishing a Charitable Gift Annuity</p>
    <p class="abs body" style="left:17px;top:351px;width:198px">You make a donation to a single charity. The gift is set aside in a reserve account and invested.</p>
    <h4 class="abs howto" style="left:17px;top:377px">How Does It Work?</h4>
    <p class="abs body" style="left:17px;top:390px;width:198px">A charitable gift annuity is a contract between a donor &amp; a charity. As a donor, you make a sizable gift to charity using cash, securities, or possibly other assets. This money is then invested. In return, you become eligible to take a partial tax deduction for your donation, plus you receive a fixed stream of income from the charity for the rest of your life. At the end of your life (as well as your spouse’s, if you’re giving as a couple), the charity receives the remainder of the gift.</p>
  </div>

  <!-- Crypto -->
  <div class="panel">
    <div class="badge badge--ring" style="left:17px;top:18px"><svg width="28" height="28"><use href="#i-coin"/></svg></div>
    <h3 class="abs sec-title" style="left:77px;top:17px;width:145px;font-size:10.4px;line-height:12.8px">Cryptocurrency<br>Strategic &amp; Smart</h3>
    <p class="abs sec-tag" style="left:77px;top:45px;width:145px;font-size:9px;line-height:11.4px">Consider donating Bitcoin and other cryptocurrencies to your favorite charity.</p>
    <p class="abs" style="left:17px;top:85px;width:200px;font-size:9.5px;line-height:11.9px">Bitcoin and other cryptocurrencies can be donated to charity just like other appreciated assets such as stocks and other business interests. Before you sell bitcoin &amp; donate the after-tax proceeds, consider donating your bitcoin directly to a favorite charity.</p>
    <h4 class="abs howto" style="left:17px;top:165px">How Does It Work?</h4>
    <p class="abs body" style="left:17px;top:179px;width:204px">Many donors find it useful to open a Donor-Advised Fund (DAF). This strategy includes two significant benefits, both for you and your favorite charity.</p>
    <ul class="abs body bullets" style="left:17px;top:218px;width:190px">
      <li>Your tax deduction will be equal to the fair market value of the donated bitcoin (as determined by a qualified appraisal).</li>
      <li>Your cryptocurrency donation is tax-smart because it may eliminate capital gains taxes on the value / appreciation AND your favorite charity will receive 100% of the value of the contribution.</li>
    </ul>
    <p class="abs body" style="left:17px;top:316px;width:196px">Often charities are not able to accept direct donations of bitcoin/crypto so using a DAF is a great way to donate these assets.</p>
    <div class="photo" style="top:368px;height:148px;background:linear-gradient(160deg,#6c9440 0%,#8fb25b 40%,#c9b08a 65%,#5d7f35 100%)" role="img" aria-label="Photo of a senior couple sitting on a park bench with shopping bags"></div>
    <svg class="curve" style="top:362px" height="26" viewBox="0 0 229 26" preserveAspectRatio="none" aria-hidden="true">
      <path d="M0 0H229V26Q114.5 -6 0 26Z" fill="#fff"/>
      <path d="M0 26Q114.5 -6 229 26" fill="none" stroke="#4cb848" stroke-width="3"/>
    </svg>
  </div>
</section>

</body>
</html>
```